Interior Stylist business card design needed

I need a business card for my new company in Sydney called "Liv Harrowby Designs". The business offers an interior styling and colour consultancy. My clients are generally not very design savvy (hence why they use me) and can range from being quite conservative to really wanting something "out there". They can be looking for a budget makeover or something more expensive / substantial. I'd like my business card design to be stylish (but not overly formal). I certainly don't want it to be conservative. I'd like it to stand out a bit! I don't really have any aversion to particular colours and I don't have a logo as such - my business name is really all I have.

Target Market(s)

As above - home owners, ranging from conservative to modern

Industry/Entity Type

Conservative

Contact Information for Business Card

Liv Harrowby Designs
Colour consultancy and interior styling
ph: 0417 238 605
email: livharrowby@qoralnet.net.au

Requirements
Should not have
• Old fashioned writing or motifs. No Times Roman font!!

```html
<!DOCTYPE html>
<html lang="en">
<head>
<meta charset="utf-8">
<title>Liv Harrowby Designs – Business Card</title>
<link rel="stylesheet" href="https://fonts.googleapis.com/css2?family=Open+Sans:wdth,wght@75..100,300..700&display=swap">
<style>
  :root {
    --page: #ffffff;
    --card: #000000;
    --ink: #ffffff;
    --ochre: #b59d4f;
    --gold: #e2b82a;
    --rust: #b05e3f;
    --vermilion: #e2502a;
    --teal: #5b9fb0;
    --sky: #35b5df;
    --azure: #3c9bd2;
    --slate: #566c9c;
  }
  * { margin: 0; padding: 0; box-sizing: border-box; }
  html, body {
    width: 1200px;
    height: 741px;
    overflow: hidden;
    background: var(--page);
  }
  .card {
    position: absolute;
    left: 0;
    top: 26px;
    width: 1200px;
    height: 694px;
    background: var(--card);
    color: var(--ink);
    font-family: "Open Sans", Arial, sans-serif;
  }
  .identity {
    position: absolute;
    left: 100px;
    width: 600px;
    top: 218px;
    text-align: center;
  }
  .business-name {
    font-size: 58px;
    font-weight: 700;
    line-height: 1;
    letter-spacing: 0.2px;
  }
  .tagline {
    margin-top: 12px;
    font-size: 31px;
    font-weight: 300;
    font-stretch: 75%;
    line-height: 1;
  }
  .contact {
    position: absolute;
    left: 100px;
    width: 600px;
    top: 412px;
    text-align: center;
    list-style: none;
    font-size: 37px;
    font-weight: 300;
    line-height: 1;
  }
  .contact li + li { margin-top: 42px; }
  .colour-swatches {
    position: absolute;
    left: 703px;
    top: 55px;
    width: 497px;
    height: 584px;
  }
</style>
</head>
<body>
  <main class="card">
    <header class="identity">
      <h1 class="business-name">Liv Harrowby Designs</h1>
      <p class="tagline">Colour Consultancy &amp; Interior Styling</p>
    </header>
    <ul class="contact">
      <li class="phone">0417 238 605</li>
      <li class="email">livharrowby@qoralnet.net.au</li>
    </ul>
    <svg class="colour-swatches" viewBox="0 0 497 584" role="img" aria-label="Painted brush-stroke swatches in bands of gold, orange-red and blue">
      <defs>
        <linearGradient id="swatch-bands" x1="0" y1="0" x2="0" y2="1">
          <stop offset="0" stop-color="var(--ochre)"/>
          <stop offset="0.2" stop-color="var(--gold)"/>
          <stop offset="0.34" stop-color="var(--rust)"/>
          <stop offset="0.5" stop-color="var(--vermilion)"/>
          <stop offset="0.62" stop-color="var(--teal)"/>
          <stop offset="0.76" stop-color="var(--sky)"/>
          <stop offset="0.88" stop-color="var(--azure)"/>
          <stop offset="1" stop-color="var(--slate)"/>
        </linearGradient>
      </defs>
      <rect x="0" y="0" width="497" height="584" fill="url(#swatch-bands)"/>
    </svg>
  </main>
</body>
</html>
```